IT Company requires new Business Card design.

Over the years we have had a few different business card designs. We are now due for new cards across the board for all staff. We felt this would be a good time to start fresh with a new design. Our traditional card simply had our details on the front, and a list of services on the back. We don't particularly need the list of services, we have had cards where the only thing on the rear of the card was our logo.
Feel free to be creative, we would like our tag line "Complete IT Management" to appear at some point, doesn't necessarily have to be with the logo.
I have attached samples and drafts of various previous cards we have used over the years.

```html
<!DOCTYPE html>
<html lang="en">
<head>
<meta charset="utf-8">
<title>Harbor Networks – Business Card</title>
<link rel="stylesheet" href="https://fonts.googleapis.com/css2?family=Open+Sans:wght@400;600;700;800&display=swap">
<style>
  :root {
    --slate: #5f7280;
    --slate-dark: #4d5e6a;
    --charcoal: #3a3d42;
    --ink: #3b3b3b;
    --paper: #ffffff;
    --backdrop: #e9eaee;
    --rule: #b9bec4;
  }
  * { margin: 0; padding: 0; box-sizing: border-box; }
  html, body {
    width: 1200px; height: 987px; overflow: hidden;
    background: var(--backdrop);
    font-family: "Open Sans", Arial, sans-serif;
  }
  .canvas { position: relative; width: 1200px; height: 987px; }

  .card {
    position: absolute;
    width: 680px; height: 416px;
    border-radius: 30px;
    overflow: hidden;
    box-shadow: 0 6px 18px rgba(0,0,0,0.12);
  }

  /* Back of card */
  .card-back {
    left: 460px; top: 56px;
    background: var(--slate);
    color: var(--paper);
  }
  .card-back .brand {
    position: absolute; left: 0; right: 0; top: 130px;
    display: flex; align-items: center; justify-content: center; gap: 18px;
    font-weight: 800; font-size: 52px; letter-spacing: 1px; text-transform: uppercase;
  }
  .card-back .brand-square { width: 34px; height: 34px; background: var(--paper); }
  .card-back .tagline {
    position: absolute; left: 0; right: 0; top: 250px;
    text-align: center; font-size: 17px; letter-spacing: 7px; text-transform: uppercase;
  }

  /* Front of card */
  .card-front {
    left: 60px; top: 510px;
    background: var(--paper);
  }
  .card-front .wave { position: absolute; inset: 0; }
  .card-front .brand {
    position: absolute; left: 44px; top: 70px;
    display: flex; align-items: center; gap: 14px;
    color: var(--slate);
    font-weight: 800; font-size: 34px; line-height: 1.0; text-transform: uppercase;
  }
  .card-front .brand-square { width: 30px; height: 30px; background: var(--slate); flex: none; }
  .card-front .divider {
    position: absolute; left: 368px; top: 48px; width: 1px; height: 170px;
    background: linear-gradient(var(--paper), var(--rule) 30%, var(--rule) 70%, var(--paper));
  }
  .contact { position: absolute; left: 392px; top: 50px; color: var(--ink); }
  .contact .person { color: var(--slate); font-weight: 700; font-size: 21px; }
  .contact .role { font-size: 17px; margin-bottom: 10px; }
  .contact ul { list-style: none; }
  .contact li {
    display: flex; align-items: center; gap: 9px;
    font-size: 16px; line-height: 25px;
  }
  .contact svg { width: 14px; height: 14px; fill: var(--slate); flex: none; }
  .address {
    position: absolute; left: 40px; top: 318px;
    color: var(--paper); font-size: 15px; line-height: 21px;
  }
</style>
</head>
<body>
<main class="canvas">

  <section class="card card-back" aria-label="Card back">
    <div class="brand"><span class="brand-square"></span>Harbor Networks</div>
    <p class="tagline">Complete IT Management</p>
  </section>

  <section class="card card-front" aria-label="Card front">
    <svg class="wave" viewBox="0 0 680 416" preserveAspectRatio="none" aria-hidden="true">
      <path d="M0,232 C170,232 250,310 390,352 C510,388 610,382 680,374" fill="none" stroke="var(--charcoal)" stroke-width="7"/>
      <path d="M0,244 C170,244 250,322 390,364 C510,398 610,392 680,386 L680,416 L0,416 Z" fill="var(--slate)"/>
    </svg>

    <div class="brand"><span class="brand-square"></span><span>Harbor<br>Networks</span></div>

    <div class="divider"></div>

    <div class="contact">
      <p class="person">Mark Ellison</p>
      <p class="role">Operation Manager</p>
      <ul>
        <li><svg viewBox="0 0 16 16"><path d="M3 1l3 3-2 2c1 2 3 4 5 5l2-2 3 3-2 3C6 15 1 10 1 3z"/></svg>08 9550 1184</li>
        <li><svg viewBox="0 0 16 16"><path d="M4 0h8v16H4zM5.5 2v9h5V2z"/></svg>0412 908 476</li>
        <li><svg viewBox="0 0 16 16"><path d="M4 1h8v4H4zM1 6h14v7h-3v2H4v-2H1zM5 11v3h6v-3z"/></svg>08 9550 1184</li>
        <li><svg viewBox="0 0 16 16"><path d="M1 3h14v10H1zM2.5 4.5L8 9l5.5-4.5z"/></svg>mark@harbornetworks.com.au</li>
        <li><svg viewBox="0 0 16 16"><path d="M8 1a7 7 0 100 14A7 7 0 008 1zm0 1.5c.8 0 1.7 2 1.9 4.5H6.1C6.3 4.5 7.2 2.5 8 2.5zM2.6 8.5h2c.1 2 .6 3.6 1.2 4.6A5.5 5.5 0 012.6 8.5zm0-1A5.5 5.5 0 015.8 2.9c-.6 1-1.1 2.6-1.2 4.6zm3.5 1h3.8c-.2 2.5-1.1 4.5-1.9 4.5s-1.7-2-1.9-4.5zm5.3 0h2a5.5 5.5 0 01-3.2 4.6c.6-1 1.1-2.6 1.2-4.6zm0-1c-.1-2-.6-3.6-1.2-4.6a5.5 5.5 0 013.2 4.6z"/></svg>www.harbornetworks.com.au</li>
      </ul>
    </div>

    <p class="address">Unit 4, 18 Harbour Crest Way<br>Bayfield WA 6090</p>
  </section>

</main>
</body>
</html>
```